πΈ Full Website Redesign on Wix β The Willowmere Atelier (Feminine, Sophisticated, Nature-Inspired)
Business Name: The Willowmere Atelier
Current Site: https://quorvalen.example/Tz8pLmQ (for structure reference only)
Platform: Wix
Business Type: Women-led Canadian online retail business
Location: Canada
π About The Willowmere Atelier
The Willowmere Atelier is a boutique e-commerce store specializing in roses and blooming plants, created for modern plant lovers who appreciate beauty, quality, and storytelling.
We are a small, women-led business in Ontario, Canada, and our audience is primarily women who are drawn to floral aesthetics, a calming user experience, and elevated design.
Our name β The Willowmere Atelier β represents both a curated collection of blooms and a love of thoughtful, meaningful beauty.
π» Project Overview
We are looking for a full website redesign from scratch (built on Wix) that reflects our brand identity: feminine, sophisticated, romantic, and grounded in nature.
The current version of the site was just a test layout β we now want a fresh, cohesive design vision that speaks directly to our female Canadian customer base with a clean, modern, and elegant interface.
This project is not just about functionality β itβs about crafting an experience that feels like a digital floral sanctuary.
π― What We Need
Full website design and development in Wix (you can start fresh)
Custom homepage design with storytelling and a welcoming brand vibe
Pages to include (subject to refinement):
Home
Shop (products will be added by us later)
About
Contact
FAQ / Info
Blog or Guides (optional placeholder)
Sophisticated visual branding:
Muted rose, blush, and earthy tones
Clean, modern layout with elegant typography
Feminine, natural, soft design elements (think floral details, soft lines, minimalism with warmth)
Optimized for both desktop and mobile
Set up global styles (font, color palette, button styles, etc.)
Guidance or setup for product sections using Wixβs eCommerce system
Create beautiful reusable sections (for us to duplicate later as needed)
π· Brand Style
We are aiming for a website that feels like:
A curated botanical boutique
Feminine and warm β but not overly girly
Sophisticated and soft, never cluttered
Clean but not sterile
Relaxed elegance with a focus on natural beauty
Color palette:
Muted rose
Warm blush tones
Cream, soft beige, earthy sage
Very subtle contrast β no stark black-and-white
Typography:
Elegant serif or soft sans-serif pairings
Easy to read but with character
π Technical Info
Platform: Wix
No custom coding required (Wix-native tools preferred)
We will handle product uploads
Weβll provide any imagery you request
π¦ Deliverables
Fully designed Wix website (ready to publish)
All pages complete with consistent design and layout
Mobile-responsive layout
Design system set up for future content (colors, typography, etc.)
Optional: Style guide PDF for brand reference (bonus)
π Timeline
Weβd like the website to be completed within 1-2 weeks after project start. Please let us know your availability.
β
To Apply
Please include:
Portfolio (especially if youβve done Wix, floral, feminine, or nature-inspired work)
A short message on how you'd approach this project
Timeline/availability
We're looking for someone who understands how to design for emotion, beauty, and ease β not just functionality. If you love soft colors, delicate details, and creating meaningful digital experiences for women, we'd love to hear from you.
πΈ Letβs build something beautiful together!
Rose enthusiasts

```html
<!DOCTYPE html>
<html lang="en">
<head>
<meta charset="utf-8">
<title>The Willowmere Atelier</title>
<link href="https://fonts.googleapis.com/css2?family=Libre+Caslon+Text:wght@400;700&family=Roboto:wght@400;500;700&display=swap" rel="stylesheet">
<style>
:root{
  --cream:#f6f0ea;
  --sage:#c5c49b;
  --sand:#dccdbd;
  --olive:#6b6a3b;
  --plum:#5b3b50;
  --plum-deep:#4a2f42;
  --rose:#c99aa3;
  --rose-text:#c7939b;
  --ink:#4a4046;
  --muted:#6a5f63;
  --white:#ffffff;
  --serif:"Libre Caslon Text", Georgia, serif;
  --sans:"Roboto", Arial, sans-serif;
}
*{margin:0;padding:0;box-sizing:border-box}
html,body{width:1200px;height:4092px;overflow:hidden}
body{background:var(--cream);font-family:var(--sans);color:var(--ink);position:relative}
a{color:inherit;text-decoration:none}
.section{position:absolute;left:0;width:1200px}
.btn{display:inline-flex;align-items:center;justify-content:center;background:var(--rose);color:var(--white);font-family:var(--sans);font-weight:500;font-size:15px;letter-spacing:.3px;border-radius:30px;height:48px;padding:0 32px}

/* announcement */
.announce{top:0;height:34px;background:var(--sage);color:var(--white);font-size:11px;display:flex;align-items:center;justify-content:center;gap:6px}
.announce u{font-weight:500}
/* header */
.site-header{top:34px;height:77px;background:var(--cream);font-size:13px;font-weight:500;color:var(--plum-deep)}
.site-header .menu{position:absolute;left:113px;top:30px;display:flex;align-items:center;gap:8px}
.site-header .brand{position:absolute;left:505px;top:10px;display:flex;align-items:center;gap:12px}
.brand .mark{width:35px;height:57px;background:var(--plum);border-radius:3px}
.brand .name{font-family:var(--sans);font-weight:400;font-size:18px;color:var(--muted)}
.site-header .account{position:absolute;right:113px;top:30px;display:flex;gap:22px}
.site-header .account span{display:flex;align-items:center;gap:6px}
/* hero */
.hero{top:111px;height:569px;background:radial-gradient(ellipse at 30% 40%,#f0a9a6 0%,#e79c8e 30%,#b98a78 60%,#6f7d55 100%);text-align:center;color:var(--white)}
.hero h1{font-family:var(--serif);font-weight:700;font-size:43px;line-height:50px;margin-top:170px;text-shadow:0 1px 6px rgba(0,0,0,.15)}
.hero p{font-size:16px;margin-top:10px}
.hero .btn{margin-top:32px;width:182px}
/* collection */
.collection{top:680px;height:609px;text-align:center}
.section-title{font-family:var(--serif);font-weight:700;color:var(--plum);font-size:38px;letter-spacing:.3px}
.collection .section-title{margin-top:73px}
.products{position:absolute;top:165px;left:113px;display:flex;gap:33px}
.product{width:219px}
.product .photo{height:291px;border-radius:18px}
.product h3{font-weight:500;font-size:16px;color:var(--plum-deep);margin-top:16px}
.product .price{font-size:13px;color:var(--rose-text);margin-top:8px}
/* story */
.story{top:1289px;height:562px;background:var(--sage)}
.story h2{position:absolute;left:113px;top:94px;font-family:var(--serif);font-weight:700;font-size:38px;line-height:46px;color:var(--plum)}
.story .copy{position:absolute;left:113px;top:204px;width:430px;font-size:13px;line-height:27px;color:var(--muted)}
.story .copy p+p{margin-top:12px}
.story .btn{position:absolute;left:113px;top:418px;width:152px;height:46px;font-size:14px;padding:0}
.story .photo{position:absolute;left:610px;top:76px;width:478px;height:410px;border-radius:18px;background:radial-gradient(circle at 55% 5%,#f4c35a 0%,#c98a3e 22%,#7b5e3a 50%,#4d5236 80%)}
/* blog */
.blog{top:1851px;height:572px;background:var(--sand);text-align:center}
.blog .section-title{margin-top:68px}
.posts{position:absolute;top:149px;left:113px;display:flex;gap:33px}
.post{position:relative;width:303px;height:339px;border-radius:18px;overflow:hidden;color:var(--white)}
.post .meta{position:absolute;left:0;right:0;bottom:22px;text-align:center}
.post .date{font-size:14px}
.post h3{font-size:16px;font-weight:700;line-height:23px;margin-top:6px}
/* sale */
.sale{top:2423px;height:720px}
.sale .banner{position:absolute;left:121px;top:96px;width:958px;height:524px;border-radius:18px;background:linear-gradient(120deg,#767a5e 0%,#5e6a4a 40%,#6f5f52 60%,#a9505a 85%,#5d6a45 100%);text-align:center;color:var(--white)}
.sale .kicker{font-family:var(--serif);font-size:25px;margin-top:84px}
.sale h2{font-family:var(--serif);font-weight:400;font-size:88px;line-height:104px;margin-top:6px}
.sale .btn{margin-top:16px;width:182px}
/* social */
.social{top:3143px;height:527px;background:var(--olive);text-align:center;color:var(--white)}
.social h2{font-family:var(--serif);font-weight:400;font-size:33px;line-height:50px;margin-top:74px}
.feed{position:absolute;top:202px;left:113px;width:975px;height:263px;overflow:hidden;display:flex;gap:22px}
.feed .tile{flex:0 0 265px;height:263px;border-radius:18px}
/* footer */
.footer{top:3670px;height:355px;background:var(--olive);border-top:1px solid rgba(255,255,255,.25);color:var(--white)}
.footer h4{font-family:var(--serif);font-weight:400;font-size:18px}
.footer .col{position:absolute;top:70px}
.footer ul{list-style:none;margin-top:26px;font-size:13px;line-height:28.5px}
.signup p{font-size:13px;line-height:24px;width:400px;margin-top:26px}
.signup label{display:block;font-size:12px;font-weight:500;margin-top:20px}
.signup .field{width:390px;border-bottom:1px solid rgba(255,255,255,.5);height:30px}
.signup .consent{position:absolute;top:198px;font-size:11px;display:flex;align-items:center;gap:6px;width:260px}
.signup .consent i{display:inline-block;width:10px;height:10px;border:1px solid var(--white)}
.signup .btn{position:absolute;left:270px;top:178px;width:118px;height:46px;padding:0;font-size:15px}
.legal{top:4025px;height:67px;background:var(--olive);border-top:1px solid rgba(255,255,255,.25);color:var(--white);font-size:13px}
.legal .copy{position:absolute;left:113px;top:27px}
.legal .links{position:absolute;left:778px;top:25px;display:flex;gap:25px;font-weight:500}
</style>
</head>
<body>

<div class="section announce">
  <svg width="12" height="10" viewBox="0 0 12 10" aria-hidden="true"><path d="M0 2h7v5H0zM7 4h3l2 2v1H7z" fill="#fff"/><circle cx="2.5" cy="8.5" r="1.3" fill="#fff"/><circle cx="9.5" cy="8.5" r="1.3" fill="#fff"/></svg>
  <span>Free shipping on all international orders over $35 <u>Shop Now</u></span>
</div>

<header class="section site-header">
  <div class="menu">
    <svg width="13" height="11" viewBox="0 0 13 11" aria-hidden="true"><rect y="0" width="13" height="2" fill="#4a2f42"/><rect y="4.5" width="13" height="2" fill="#4a2f42"/><rect y="9" width="13" height="2" fill="#4a2f42"/></svg>
    Menu
  </div>
  <div class="brand"><span class="mark"></span><span class="name">the willowmere atelier</span></div>
  <div class="account">
    <span><svg width="14" height="12" viewBox="0 0 14 12" aria-hidden="true"><path d="M0 1h2.5l2 7h7l2-5.5H4" fill="none" stroke="#4a2f42" stroke-width="1.6"/><circle cx="5.5" cy="10.5" r="1.2" fill="#4a2f42"/><circle cx="10.5" cy="10.5" r="1.2" fill="#4a2f42"/></svg>Cart (0)</span>
    <span><svg width="14" height="14" viewBox="0 0 14 14" aria-hidden="true"><circle cx="7" cy="7" r="6.2" fill="none" stroke="#4a2f42" stroke-width="1.4"/><circle cx="7" cy="5.5" r="2.2" fill="#4a2f42"/><path d="M3 11.5c1-2 2.4-2.8 4-2.8s3 .8 4 2.8" fill="#4a2f42"/></svg>Log In</span>
  </div>
</header>

<section class="section hero" role="img" aria-label="Close view of pink and apricot garden roses among green leaves">
  <h1>POTTED BEAUTY, READY TO<br>ROOT AT HOME</h1>
  <p>A curated collection of timeless blooms &amp; botanical beauty</p>
  <a class="btn" href="#">SHOP BLOOMS</a>
</section>

<section class="section collection">
  <h2 class="section-title">EXPLORE THE COLLECTION</h2>
  <div class="products">
    <div class="product">
      <div class="photo" role="img" aria-label="Pale peach roses on a leafy bush" style="background:linear-gradient(160deg,#f2d6c6 0%,#e9b9a2 40%,#4e6a3a 100%)"></div>
      <h3>Marlowe Blush</h3><div class="price">C$31.99</div>
    </div>
    <div class="product">
      <div class="photo" role="img" aria-label="Yellow rose shrub in garden soil" style="background:linear-gradient(160deg,#e9b23a 0%,#6f7a34 45%,#3e4a26 100%)"></div>
      <h3>Marlowe Blush</h3><div class="price">C$31.99</div>
    </div>
    <div class="product">
      <div class="photo" role="img" aria-label="Single orange rose in full bloom" style="background:radial-gradient(circle at 50% 45%,#f39a6b 0%,#e5804f 40%,#5c7340 100%)"></div>
      <h3>Marlowe Blush</h3><div class="price">C$31.99</div>
    </div>
    <div class="product">
      <div class="photo" role="img" aria-label="Apricot rose with cream outer petals" style="background:radial-gradient(circle at 50% 50%,#f6c27f 0%,#f2d9b4 45%,#3d5130 100%)"></div>
      <h3>Marlowe Blush</h3><div class="price">C$31.99</div>
    </div>
  </div>
</section>

<section class="section story">
  <h2>OUR JOURNEY FROM<br>SEED TO BLOSSOM</h2>
  <div class="copy">
    <p>The Willowmere Atelier is dedicated to providing a curated collection of roses and blooming plants, carefully selected to bring joy and elegance to your home garden.</p>
    <p>Our team is committed to sharing our passion for plants and fostering a community of plant enthusiasts. Join us in celebrating the beauty of nature and the art of plant care.</p>
  </div>
  <a class="btn" href="#">OUR MISSION</a>
  <div class="photo" role="img" aria-label="Gardener holding a bouquet of red roses in warm sunset light"></div>
</section>

<section class="section blog">
  <h2 class="section-title">OUR PLANT CARE BLOG</h2>
  <div class="posts">
    <article class="post" role="img" aria-label="Orange gerbera flower by a window" style="background:linear-gradient(180deg,#c9cdc0 0%,#d7683e 45%,#4a5a34 100%)">
      <div class="meta"><div class="date">25 July 2025</div><h3>Lorem ipsum amet, consectetur<br>adipiscing dolor sit</h3></div>
    </article>
    <article class="post" role="img" aria-label="Gardener misting potted flowers on a porch" style="background:linear-gradient(180deg,#8a8478 0%,#9a6a7a 50%,#5b4a5a 100%)">
      <div class="meta"><div class="date">25 July 2025</div><h3>Lorem ipsum amet, consectetur<br>adipiscing dolor sit</h3></div>
    </article>
    <article class="post" role="img" aria-label="Gloved hands planting a red rose bush" style="background:linear-gradient(180deg,#4f7a3a 0%,#b7393e 45%,#3e3a2e 100%)">
      <div class="meta"><div class="date">25 July 2025</div><h3>Lorem ipsum amet, consectetur<br>adipiscing dolor sit</h3></div>
    </article>
  </div>
</section>

<section class="section sale">
  <div class="banner" role="img" aria-label="Gardener tending red roses in a green garden">
    <div class="kicker">Happening Now</div>
    <h2>WEEKEND<br>SALE</h2>
    <a class="btn" href="#">SHOP BLOOMS</a>
  </div>
</section>

<section class="section social">
  <h2>Follow Us<br>@THE WILLOWMERE ATELIER</h2>
  <div class="feed">
    <div class="tile" role="img" aria-label="Woman in a straw hat holding a potted plant" style="background:linear-gradient(160deg,#efe9e2 0%,#d98a55 55%,#a25a34 100%)"></div>
    <div class="tile" role="img" aria-label="Two women holding potted plants in a greenhouse" style="background:linear-gradient(160deg,#4f5e3d 0%,#c07a5a 55%,#6e5a4a 100%)"></div>
    <div class="tile" role="img" aria-label="Climbing bush of pale pink roses" style="background:linear-gradient(160deg,#5c7a3e 0%,#e7cfc4 50%,#3f5a2e 100%)"></div>
    <div class="tile" role="img" aria-label="Yellow roses among leaves" style="background:linear-gradient(160deg,#5c7a3e 0%,#f2d557 50%,#3f5a2e 100%)"></div>
  </div>
</section>

<footer class="section footer">
  <div class="col signup" style="left:113px">
    <h4>Stay inspired and eco-conscious</h4>
    <p>Receive the latest trends and tips on eco-friendly design, sustainable living, zero waste and eco-conscious practices.</p>
    <label>Email *</label>
    <div class="field"></div>
    <div class="consent"><i></i>Yes, subscribe me to your newsletter. *</div>
    <a class="btn" href="#">SUBMIT</a>
  </div>
  <div class="col" style="left:601px"><h4>Shop</h4><ul><li>Shop All</li><li>Plants</li><li>Pots</li><li>Sale</li></ul></div>
  <div class="col" style="left:764px"><h4>Helpful Links</h4><ul><li>FAQ</li><li>Shipping &amp; Returns</li><li>Terms &amp; Conditions</li><li>Payment Methods</li></ul></div>
  <div class="col" style="left:996px"><h4>Company</h4><ul><li>Our Story</li><li>Contact Us</li><li>Gift Card</li><li>Subscriptions</li></ul></div>
</footer>

<div class="section legal">
  <div class="copy">© 2035 The Willowmere Atelier.</div>
  <div class="links"><a href="#">Leafline</a><a href="#">Petalnote</a><a href="#">Stemcast</a><a href="#">Gardenboard</a></div>
</div>

</body>
</html>
```